PWNF Traditional Business Card Project

Please see attached....just a simple business card... on attachment- please use the exact font, style, etc as the attached "Ned Farley Broughton" card... however, replace with the "Walter Augustin Pryde" text and address below the card.

```html
<!DOCTYPE html>
<html lang="en">
<head>
<meta charset="utf-8">
<title>PWNF Business Card</title>
<link rel="stylesheet" href="https://fonts.googleapis.com/css2?family=Cinzel:wght@400;500&family=Montserrat:wght@300;400&display=swap">
<style>
  :root {
    --stage: #3b3b3b;
    --card: #dddad7;
    --ink: #1b1b1b;
    --ink-soft: #3a3a3a;
    --ghost: #cfccc9;
    --rule: #8d8a87;
  }
  * { margin: 0; padding: 0; box-sizing: border-box; }
  html, body { width: 1200px; height: 880px; overflow: hidden; }
  body {
    background: var(--stage);
    display: flex;
    flex-direction: column;
    align-items: center;
    justify-content: center;
    gap: 56px;
  }
  .card {
    position: relative;
    width: 620px;
    height: 354px;
    background: var(--card);
    border-radius: 18px;
    overflow: hidden;
    color: var(--ink);
  }

  /* Front */
  .front-decor {
    position: absolute;
    right: 40px;
    top: 24px;
    width: 170px;
    height: 190px;
    border-radius: 12px;
    background: linear-gradient(160deg, var(--ghost), #d6d3d0);
  }
  .firm {
    position: absolute;
    left: 70px;
    top: 150px;
  }
  .firm-name {
    font-family: "Cinzel", serif;
    font-size: 34px;
    font-weight: 500;
    letter-spacing: 0.5px;
    color: var(--ink);
  }
  .firm-sub {
    font-family: "Montserrat", sans-serif;
    font-weight: 300;
    font-size: 15px;
    letter-spacing: 7.5px;
    margin-top: 2px;
    color: var(--ink-soft);
  }
  .firm-url {
    position: absolute;
    left: 250px;
    top: 282px;
    font-family: "Montserrat", sans-serif;
    font-weight: 400;
    font-size: 13px;
    letter-spacing: 2.5px;
    color: var(--ink-soft);
  }

  /* Back */
  .brand-name {
    position: absolute;
    left: 70px;
    top: 150px;
    width: 200px;
    text-align: center;
    font-family: "Cinzel", serif;
    font-weight: 500;
    font-size: 36px;
    line-height: 44px;
    color: var(--ink);
  }
  .divider {
    position: absolute;
    left: 310px;
    top: 78px;
    width: 1px;
    height: 212px;
    background: var(--rule);
  }
  .contact {
    position: absolute;
    left: 336px;
    top: 78px;
  }
  .person-name {
    font-family: "Cinzel", serif;
    font-size: 19px;
    font-weight: 500;
    color: var(--ink);
  }
  .person-title {
    font-family: "Montserrat", sans-serif;
    font-weight: 300;
    font-size: 12px;
    letter-spacing: 3.5px;
    color: var(--ink-soft);
    margin: 2px 0 0 18px;
  }
  .lines {
    list-style: none;
    margin: 12px 0 0 18px;
    font-family: "Montserrat", sans-serif;
    font-size: 13px;
    line-height: 19px;
    color: var(--ink);
  }
  .lines li { display: flex; align-items: center; gap: 8px; }
  .lines svg { width: 11px; height: 11px; fill: var(--ink); flex: none; }
  .address {
    margin: 12px 0 0 18px;
    font-family: "Montserrat", sans-serif;
    font-size: 13px;
    line-height: 19px;
    color: var(--ink);
  }
</style>
</head>
<body>

<section class="card card-front">
  <div class="front-decor" role="img" aria-label="Faint firm monogram decoration"></div>
  <div class="firm">
    <div class="firm-name">Pinewood Northfield</div>
    <div class="firm-sub">LAWYERS GROUP, PLC</div>
  </div>
  <div class="firm-url">WWW.PWNFLAW.COM</div>
</section>

<section class="card card-back">
  <div class="brand-name">PWNF</div>
  <div class="divider"></div>
  <div class="contact">
    <div class="person-name">Walter Augustin Pryde</div>
    <div class="person-title">ATTORNEY AT LAW</div>
    <ul class="lines">
      <li>
        <svg viewBox="0 0 24 24" aria-hidden="true"><path d="M6.6 10.8a15.1 15.1 0 0 0 6.6 6.6l2.2-2.2a1 1 0 0 1 1-.25 11.4 11.4 0 0 0 3.6.57 1 1 0 0 1 1 1V20a1 1 0 0 1-1 1A17 17 0 0 1 3 4a1 1 0 0 1 1-1h3.5a1 1 0 0 1 1 1c0 1.250.2 2.450.57 3.570a1 1 0 0 1-.25 1z"/></svg>
        (555) 014-2200
      </li>
      <li>
        <svg viewBox="0 0 24 24" aria-hidden="true"><path d="M6 2h12v5H6zM3 9h18v9h-3v4H6v-4H3zm5 7v4h8v-4z"/></svg>
        (555) 014-2201
      </li>
      <li>
        <svg viewBox="0 0 24 24" aria-hidden="true"><path d="M2 4h20v16H2zm2 2v.5l8 5.5 8-5.5V6zm0 2.9V18h16V8.9l-8 5.5z"/></svg>
        pryde@pwnflaw.com
      </li>
    </ul>
    <div class="address">
      1420 Alder Court, Suite B<br>
      Marlow Heights, CA 91000<br>
      www.pwnflaw.com
    </div>
  </div>
</section>

</body>
</html>
```